Plume Dishwasher Pods (Pack design) *

We require a doy pack design for a new dishwasher pod brand. It aims at competing with the top tier global brands, and hence needs to have 'big brand feel'. The product is of high quality, slightly lower priced and hence makes "Plume" for the consumer to purchase.

The design should be clean, sophisticated, modern, and appeal to the upper end consumer.

What's important, is that the consumer is habitually buying the known-brand, and hence we need to quickly and visually establish what the product is (dishwashing tablet) and also establish trust (the product will deliver). Hence we can borrow equity from category cues (see design brief)

Target Market(s)

Upper LSM (mid to higher end of the market). Dishwasher penetration is low, and hence only the top end of the market has a dishwasher

Industry/Entity Type

Cleaning Product

Font styles to use
Sans Serif

Colors
ffffff
000000
0255a3
33a6d7
fbee3d
add136

Requirements
Must have
• Message/Idea/Visual Hierarchy:
• Priority 1: Category / Product Type (i.e. "Dishwasher Pods"). Category most important, then the brand name. Could be joined. This must be clear, and stand out!
• Priority 2: Efficient cleaning pod/tablet which cleans thoroughly (scienctific cues, sparkles, foam, lemon/lime, etc.). Please use 3D art, rather than flat artwork. The idea that we may be well priced, but the technology is state-of-the-art. People are taking a risk buying us, so we need to comfort them that the product will work! We need to establish brand trust with our serious and professional look.
• Priority 3: Stand-out, bold, clean, modern, simple design. Simple doesn't mean "no class and style". Competitors have busy packaging with lots of colours and text.
• Lastly: We are "sensible" (in terms of cost and efficiency), "conscious", "have values". We may partner with a "Save Water" organisation. Hence the feeling of "values" and the "human touch" is a nice-to-have. We may be serious in packaging, but we care about you, your pocket, society and the environment. Hence you can contact us on chirpa for instant-chat (see packagaing text).
Nice to have
• - A simple placeholder 'back of pack' text "Lorem ipsum". No need for excessive design, this will be worked upon in Round 2 with the winning design(er).
• - In a world where clean modern and computers dominate, there can be perfection in imperfection. There can be a personal (human) touch added. Think detailed droplets, or 3D/natural feel.
• - Dummy barcode
• - As for the colours, we are very open to ideas and the given colours in the project was only a guideline. Don't necessarily stick to them - we encourage creativity.
Should not have
• The brand is not:
• - Cheap and cheesy and cartoonish (as most competitors). Instead we are 3D, real!
• - Busy and tiring on the eye (as the lead competitor). It can be bold, stylish, eye-catching, but not overly busy and dainty. Think of Fennix (infancy days) vs Wumbo (market leader days).

```html
<!DOCTYPE html>
<html lang="en">
<head>
<meta charset="utf-8">
<title>Plume Dishwasher Pods – Pack Front</title>
<link href="https://fonts.googleapis.com/css2?family=Lato:wght@400;700;900&display=swap" rel="stylesheet">
<style>
  :root {
    --bg: #eceef0;
    --pack: #fbfbfb;
    --pack-edge: #e3e5e7;
    --brand-blue: #1b82bf;
    --ink: #232323;
    --ink-soft: #555a5e;
    --icon-blue: #2a7fb8;
    --art-blue: #2f95d0;
    --art-sky: #7cc4ea;
    --art-violet: #8a72c4;
    --art-mesh: #c9d6ea;
  }
  html, body {
    margin: 0;
    width: 1200px;
    height: 1000px;
    overflow: hidden;
    background: var(--bg);
    font-family: "Lato", Arial, sans-serif;
  }
  .canvas {
    position: relative;
    width: 1200px;
    height: 1000px;
  }
  .pack {
    position: absolute;
    left: 357px;
    top: 92px;
    width: 374px;
    height: 627px;
    transform: scale(1.3);
    transform-origin: top left;
    background: var(--pack);
    border-radius: 10px 10px 6px 6px;
    box-shadow: inset 0 0 0 1px var(--pack-edge);
    overflow: hidden;
  }
  .pack__zip {
    position: absolute;
    left: 0; right: 0; top: 44px;
    height: 1px;
    background: var(--pack-edge);
  }
  .hero-art {
    position: absolute;
    left: 40px; top: 222px;
    width: 304px;
    height: 345px;
  }
  .brand {
    position: absolute;
    left: 58px; top: 148px;
    margin: 0;
    font-weight: 700;
    font-size: 25px;
    letter-spacing: 0.5px;
    color: var(--brand-blue);
  }
  .category {
    position: absolute;
    left: 57px; top: 178px;
    margin: 0;
    font-weight: 900;
    font-size: 36px;
    line-height: 37px;
    color: var(--ink);
    letter-spacing: 0.2px;
  }
  .descriptor {
    position: absolute;
    left: 59px; top: 257px;
    margin: 0;
    font-size: 9.5px;
    letter-spacing: 0.2px;
    color: var(--ink-soft);
  }
  .claims {
    position: absolute;
    left: 66px; top: 546px;
    margin: 0; padding: 0;
    list-style: none;
  }
  .claims li {
    display: flex;
    align-items: center;
    gap: 16px;
    height: 21px;
    font-size: 5.5px;
    color: var(--ink-soft);
  }
  .claims .icon {
    width: 8px; height: 8px;
    border-radius: 2px;
    background: var(--icon-blue);
  }
  .claims .icon--round { border-radius: 50%; }
  .net {
    position: absolute;
    left: 284px; top: 568px;
    color: var(--ink);
  }
  .net__count { font-size: 10px; font-weight: 700; }
  .net__count small { font-size: 7px; }
  .net__weight { font-size: 6.5px; font-weight: 700; margin-top: 1px; }
  .social {
    position: absolute;
    left: 270px; top: 600px;
    display: flex;
    gap: 4px;
    font-size: 6px;
    line-height: 8px;
    color: var(--icon-blue);
  }
  .social__dot {
    width: 7px; height: 7px;
    border-radius: 50%;
    background: var(--icon-blue);
    margin-top: 1px;
  }
</style>
</head>
<body>
<main class="canvas">
  <section class="pack">
    <div class="pack__zip"></div>

    <svg class="hero-art" viewBox="0 0 304 345" role="img" aria-label="3D illustration of glossy blue and violet molecules linked in a network over a faint wireframe mesh">
      <defs>
        <radialGradient id="artMesh" cx="0.5" cy="0.45" r="0.6">
          <stop offset="0" stop-color="var(--art-mesh)" stop-opacity="0.7"/>
          <stop offset="1" stop-color="var(--art-mesh)" stop-opacity="0"/>
        </radialGradient>
        <radialGradient id="artBlue" cx="0.45" cy="0.55" r="0.45">
          <stop offset="0" stop-color="var(--art-blue)" stop-opacity="0.95"/>
          <stop offset="0.45" stop-color="var(--art-sky)" stop-opacity="0.7"/>
          <stop offset="1" stop-color="var(--art-sky)" stop-opacity="0"/>
        </radialGradient>
        <radialGradient id="artViolet" cx="0.78" cy="0.4" r="0.32">
          <stop offset="0" stop-color="var(--art-violet)" stop-opacity="0.85"/>
          <stop offset="1" stop-color="var(--art-violet)" stop-opacity="0"/>
        </radialGradient>
      </defs>
      <rect width="304" height="345" fill="url(#artMesh)"/>
      <rect width="304" height="345" fill="url(#artBlue)"/>
      <rect width="304" height="345" fill="url(#artViolet)"/>
    </svg>

    <p class="brand">PLUME</p>
    <h1 class="category">DISHWASHER<br>PODS</h1>
    <p class="descriptor">Automatic Dishwasher Detergent</p>

    <ul class="claims">
      <li><span class="icon"></span>Suitable for all washing machines</li>
      <li><span class="icon icon--round"></span>Environmentally friendly</li>
      <li><span class="icon icon--round"></span>Washing quality</li>
    </ul>

    <div class="net">
      <div class="net__count">44 <small>Pods</small></div>
      <div class="net__weight">Weight: 500g</div>
    </div>

    <div class="social">
      <span class="social__dot"></span>
      <span>@PlumeHome<br>on chirpa</span>
    </div>
  </section>
</main>
</body>
</html>
```